tinyTally Resource Book - 10 maths tasks to do outside

I need a 22 (11 pages back to back) page A6 sized book produced to standard for submission to professional printer. Needs to be as .pdf file showing guide lines and allowances for colour bleed. I have text already written and submitted as attachment in a Word file with margins set to A6 size. The theme of the materials is "Nature Play" so using lots of pictures from nature (Australia preferably) and showing lots of patterns in nature (rocks, leaves, flower petals etc). Some of the tasks refer to specific activities, such as "shadows" and "floating" so would be great to illustrate appropriately. The big emphasis is on learning outside the classroom, getting kids to engage actively with nature. I would like to see the pages as full colour - so not white background. The book itself will be spiral bound along the top edge so a margin of at least 1cm will be required at the top of each page (or the bottom of even numbered pages). Book will be printed on plastic laminated matte paper for outdoor use. Font size needs to be big enough to read. Fonts sizes, alignments and page numbers are all different at the moment and need to be standardised. One photo is included in a page as a sample if you can use it, otherwise disregard. Logo for Wattlebrook Numeracy Guild is also included to have as part of the acknowledgements at the back of the book.

Target Market(s)

Book is for early childhood and preschool teachers.

Industry/Entity Type

Education

Font styles to use
Sans Serif

Requirements
Must have
• Colour and appeal.
Nice to have
• Use of natural colours instead of bright catchy colours but that is your call.
Should not have
• American spelling

```html
<!DOCTYPE html>
<html lang="en-AU">
<head>
<meta charset="utf-8">
<title>tinyTally – 4. One More</title>
<link rel="stylesheet" href="https://fonts.googleapis.com/css2?family=Jost:ital,wght@0,400;0,800;1,700&display=swap">
<style>
  :root {
    --paper: #ffffff;
    --trim-line: #3a3a3a;
    --wood-light: #f3c88f;
    --wood-mid: #ecbb7c;
    --wood-deep: #e2ab68;
    --heading-blue: #2f3f95;
    --body-ink: #3a3128;
    --bullet-red: #d62b2b;
    --badge-text: #ffffff;
  }
  * { box-sizing: border-box; margin: 0; padding: 0; }
  html, body { width: 892px; height: 1200px; overflow: hidden; background: var(--paper); }
  .sheet { position: relative; width: 892px; height: 1200px; font-family: "Jost", sans-serif; }
  .crop-marks { position: absolute; inset: 0; }
  .page {
    position: absolute; left: 53px; top: 56px; width: 787px; height: 1092px;
    background: linear-gradient(100deg, var(--wood-deep) 0%, var(--wood-light) 30%, var(--wood-mid) 55%, var(--wood-light) 80%, var(--wood-deep) 100%);
  }
  .page-title, .outcome {
    position: absolute; left: 0; right: 0; text-align: center;
    font-weight: 800; color: var(--heading-blue);
    text-shadow: 1px 1px 0 #fff, -1px -1px 0 #fff, 1px -1px 0 #fff, -1px 1px 0 #fff, 2px 2px 2px rgba(0,0,0,.25);
  }
  .page-title { top: 46px; font-size: 46px; line-height: 60px; }
  .outcome { top: 116px; font-size: 31px; line-height: 42px; padding: 0 60px; }
  .section-label {
    position: absolute; left: 73px; font-style: italic; font-weight: 700;
    font-size: 24px; line-height: 30px; color: var(--heading-blue);
  }
  .body-text {
    position: absolute; left: 143px; font-size: 31px; line-height: 45.5px; color: var(--body-ink);
  }
  .aims { position: absolute; left: 133px; top: 594px; list-style: none; }
  .aims li {
    position: relative; padding-left: 32px; font-size: 30px; line-height: 42px;
    color: var(--body-ink);
  }
  .aims li::before {
    content: ""; position: absolute; left: 2px; top: 12px; width: 16px; height: 16px;
    background: var(--bullet-red); transform: rotate(45deg);
  }
  .page-badge { position: absolute; left: 641px; top: 930px; width: 74px; height: 70px; }
</style>
</head>
<body>
<div class="sheet">
  <svg class="crop-marks" width="892" height="1200" aria-hidden="true">
    <g stroke="var(--trim-line)" stroke-width="1">
      <line x1="53" y1="0" x2="53" y2="36"/><line x1="0" y1="53" x2="36" y2="53"/>
      <line x1="74" y1="36" x2="74" y2="74"/><line x1="36" y1="74" x2="74" y2="74"/>
      <line x1="839" y1="0" x2="839" y2="36"/><line x1="856" y1="53" x2="892" y2="53"/>
      <line x1="818" y1="36" x2="818" y2="74"/><line x1="818" y1="74" x2="856" y2="74"/>
      <line x1="53" y1="1164" x2="53" y2="1200"/><line x1="0" y1="1147" x2="36" y2="1147"/>
      <line x1="74" y1="1126" x2="74" y2="1164"/><line x1="36" y1="1126" x2="74" y2="1126"/>
      <line x1="839" y1="1164" x2="839" y2="1200"/><line x1="856" y1="1147" x2="892" y2="1147"/>
      <line x1="818" y1="1126" x2="818" y2="1164"/><line x1="818" y1="1126" x2="856" y2="1126"/>
    </g>
  </svg>

  <div class="page" role="img" aria-label="Light bamboo wood-grain background">
    <h1 class="page-title">4. One More</h1>
    <h2 class="outcome">EYLF – Outcome 2: Children are connected with and contribute to their world</h2>

    <p class="section-label" style="top:258px">Children become aware of fairness when they...</p>
    <p class="body-text" style="top:295px">are empowered to make choices<br>and problem solve to meet their<br>needs in particular contexts</p>

    <p class="section-label" style="top:432px">Educators promote this learning when they...</p>
    <p class="body-text" style="top:468px">engage children in discussions about<br>respectful and equal relations</p>

    <p class="section-label" style="top:558px">This task provides an opportunity to:</p>
    <ul class="aims" style="left:133px">
      <li>explore the concepts of “equal” and<br>“more”</li>
      <li>discuss how inequity<br>happens</li>
      <li>explore sharing equally</li>
      <li>develop strategies for<br>dealing with inequity</li>
    </ul>

    <svg class="page-badge" viewBox="0 0 74 70" aria-label="Page 8">
      <polygon points="37,0 74,27 60,70 14,70 0,27" fill="var(--heading-blue)"/>
      <text x="37" y="52" text-anchor="middle" font-family="Jost, sans-serif" font-size="32" fill="var(--badge-text)">8</text>
    </svg>
  </div>
</div>
</body>
</html>
```